Luxury Business Card Design for High-End Window Treatments

Gilded Slatworks
Custom Plantation Shutters & Architectural Shading Systems

⸻

BACK

Daniel Trevick
Owner

Custom Interior & Exterior Window Treatments

919-555-0148
gildedslatworks.com

I have included a picture that I’m hoping we can use on the back, but I’m also wondering if you can get rid of the ladder? Should we get rid of shutters , shades and blinds underneath Gilded Slatworks?

Target Market(s)

High-end residential homeowners, custom home builders, architects, interior designers, and luxury renovation clients seeking premium plantation shutters and motorized architectural shading systems.

Industry/Entity Type

Custom Window treatments

Contact Information for Business Card

Front Gilded Slatworks Custom Plantation Shutters Motorized Architectural Shading Systems BACK Daniel Trevick Owner 919-555-0148 GildedSlatworks.com Custom Interior & Exterior Window Treatments By Appointment

Requirements
Nice to have
• Not 100% sure on nice to halves or the color but you can definitely check out my website to get a better understanding of what I’m trying to do

```html
<!DOCTYPE html>
<html lang="en">
<head>
<meta charset="utf-8">
<title>Gilded Slatworks – Business Card</title>
<link rel="stylesheet" href="https://fonts.googleapis.com/css2?family=Open+Sans:wght@300;400;600;700;800&display=swap">
<style>
  :root {
    --stage: #0d0d0d;
    --card: #1b1b1b;
    --gold: #c9a234;
    --gold-light: #f1d27a;
    --gold-deep: #a47a16;
    --white: #ffffff;
    --sky: #5a9fe0;
    --roof: #e9e3d6;
    --shade: #2c3038;
  }
  * { box-sizing: border-box; margin: 0; padding: 0; }
  html, body { width: 1200px; height: 963px; overflow: hidden; background: var(--stage); }
  body { font-family: "Open Sans", sans-serif; position: relative; }

  .card {
    position: absolute;
    left: 250px;
    width: 700px;
    height: 400px;
    background: var(--card);
    box-shadow: 0 10px 30px rgba(0,0,0,.6);
  }
  .card--front { top: 54px; }
  .card--back { top: 509px; }

  .card__frame {
    position: absolute;
    inset: 22px;
    border: 2px solid var(--gold);
  }

  /* front */
  .card__photo {
    position: absolute;
    inset: 34px;
    background: linear-gradient(180deg, var(--sky) 0%, #8cb7d8 22%, var(--roof) 34%, var(--shade) 45%, #3a3a3c 70%, #5b4a3a 100%);
  }
  .card__caption {
    position: absolute;
    left: 40px;
    bottom: 40px;
    padding: 2px 10px;
    color: var(--white);
    font-weight: 700;
    font-size: 17px;
    letter-spacing: .2px;
    text-shadow: 0 1px 3px rgba(0,0,0,.7);
  }

  /* back */
  .card__frame--back { border-color: var(--gold); }
  .card__tagline {
    position: absolute;
    left: 72px;
    bottom: 12px;
    padding: 0 12px;
    background: var(--card);
    color: var(--white);
    font-weight: 300;
    font-size: 19px;
    letter-spacing: .3px;
  }
  .brand {
    position: absolute;
    left: 70px;
    top: 118px;
    width: 290px;
    text-align: center;
  }
  .brand__name {
    color: var(--gold);
    font-weight: 400;
    font-size: 38px;
    line-height: 1.1;
  }
  .brand__services {
    margin-top: 10px;
    color: var(--gold);
    font-weight: 400;
    font-size: 17px;
    word-spacing: 14px;
  }
  .divider {
    position: absolute;
    left: 378px;
    top: 110px;
    width: 2px;
    height: 170px;
    background: var(--gold);
    transform: rotate(28deg);
  }
  .contact {
    position: absolute;
    left: 420px;
    top: 118px;
    color: var(--white);
  }
  .contact__name {
    color: var(--gold-light);
    font-weight: 800;
    font-size: 27px;
    letter-spacing: .5px;
    text-transform: uppercase;
  }
  .contact__title {
    font-weight: 300;
    font-size: 20px;
    margin-bottom: 26px;
  }
  .contact__line {
    display: flex;
    align-items: center;
    gap: 8px;
    font-weight: 300;
    font-size: 20px;
    line-height: 1.45;
  }
  .contact__icon { width: 16px; height: 16px; flex: none; }
</style>
</head>
<body>

  <section class="card card--front" aria-label="Card front">
    <div class="card__photo" role="img" aria-label="Photograph of a home porch with motorized exterior shades under a blue sky"></div>
    <div class="card__frame"></div>
    <p class="card__caption">Custom Plantation Shutters &amp; Motorized Architectural Shading Systems</p>
  </section>

  <section class="card card--back" aria-label="Card back">
    <div class="card__frame card__frame--back"></div>
    <p class="card__tagline">Custom Interior &amp; Exterior Window Treatments</p>

    <div class="brand">
      <p class="brand__name">Gilded<br>Slatworks</p>
      <p class="brand__services">Shutters Shades Blinds</p>
    </div>

    <div class="divider"></div>

    <div class="contact">
      <p class="contact__name">Daniel Trevick</p>
      <p class="contact__title">Owner</p>
      <p class="contact__line">
        <svg class="contact__icon" viewBox="0 0 16 16" aria-hidden="true">
          <path fill="var(--gold)" d="M3.5 1.5l2.5 0 1 3.5-1.6 1.1a8 8 0 0 0 4.5 4.5L11 9l3.5 1v2.5c0 1-1 2-2 2C6.5 14.5 1.5 9.5 1.5 3.5c0-1 1-2 2-2z"/>
        </svg>
        919-555-0148
      </p>
      <p class="contact__line">
        <svg class="contact__icon" viewBox="0 0 16 16" aria-hidden="true">
          <circle cx="8" cy="8" r="7" fill="none" stroke="var(--gold)" stroke-width="1.5"/>
          <ellipse cx="8" cy="8" rx="3" ry="7" fill="none" stroke="var(--gold)" stroke-width="1.2"/>
          <line x1="1" y1="8" x2="15" y2="8" stroke="var(--gold)" stroke-width="1.2"/>
        </svg>
        gildedslatworks.com
      </p>
    </div>
  </section>

</body>
</html>
```